Website for Vornelix Capital, my new firm that raises money from investors to buy, build, own an...

Vornelix Capital needs a website! We are a new company with very experienced people, who invest in, own and build hotel properties, as well as apartments and other commercial real estate. We seek investors for our projects, and we provide safe, secure returns on their investment in our projects. Our new logo is designed to exhibit strength, class and security, and would like our website to continue on this theme. Our name, Vornelix, is a word-play on a Greek word “aristeia”, which means “excellence” and “a warriors finest moment of glory in war”. If you are in business, you realize that much of it is like war, with strategy and moves and opponents and competitors, and ever-changing economic conditions and threats that make business very much like war. We like to think that we are good at business (war), and so have named our company “Vornelix”, using the founders last name and the word “aristeia” combined. Another definition of "aristeia" is "performing at the peak of one's potential after a long struggle"...again, much like business in real life! The website design should exhibit financial security, smart moves, and positive growth towards a bright future.

Target Market(s)

The target market is smart and wealthy investors, with others such as brokers, cities and government agencies, lenders, sellers, partners, etc also looking at it.

Industry/Entity Type

Investment

Number of Pages Required

5+ page

Font styles to use
Sans Serif

Colors
fec214

Requirements
Must have
• Our website should have a landing page, a "about" or bio page, a projects page and a contact us page. Our new logo uses the colors black and gold, so this should be factored in to our site. The site should be simple, yet impactful and impressive. I have actually two logos, which can be mixed and interchanged in a complimentary way, each with their own unique look.
Nice to have
• I have uploaded a couple screenshots of a website i like, and the simplicity I mention.
Should not have
• The site should not be flashy or complicated or complex or "busy"

```html
<!DOCTYPE html>
<html lang="en">
<head>
<meta charset="utf-8">
<title>Vornelix Capital</title>
<link href="https://fonts.googleapis.com/css2?family=Poppins:ital,wght@0,400;0,500;0,600;0,700;1,400&display=swap" rel="stylesheet">
<style>
:root{
  --gold:#fec214;
  --gold-deep:#f5b400;
  --navy:#1b2150;
  --ink:#151515;
  --text:#2b2b2b;
  --muted:#555;
  --white:#fff;
  --footer:#12162b;
}
*{margin:0;padding:0;box-sizing:border-box}
html,body{width:1200px;height:3279px;overflow:hidden}
body{font-family:'Poppins',sans-serif;color:var(--text);background:var(--white);position:relative}
.abs{position:absolute}
.btn{position:absolute;background:var(--gold);color:var(--white);font-weight:600;border-radius:26px;display:flex;align-items:center;justify-content:center;box-shadow:0 3px 8px rgba(0,0,0,.15)}

/* hero */
.hero{position:absolute;left:0;top:0;width:1200px;height:682px;background:linear-gradient(180deg,#26306e 0%,#3a3f6a 45%,#5a4636 80%,#3b2c24 100%)}
.hero-shade{position:absolute;inset:0;background:linear-gradient(90deg,rgba(20,26,70,.55),rgba(20,26,70,.15) 50%,rgba(20,26,70,.5))}
.brand{position:absolute;left:95px;top:58px;display:flex;align-items:center;gap:10px;color:var(--white);font-weight:600;font-size:30px;letter-spacing:1px}
.brand-mark{width:16px;height:16px;background:var(--white)}
.nav{position:absolute;top:70px;left:742px;display:flex;gap:30px;color:var(--white);font-size:16px}
.nav .active{font-weight:600}
.hero-title{position:absolute;top:275px;left:0;width:1200px;text-align:center;color:var(--white);font-size:50px;font-weight:700;letter-spacing:1px}
.hero-sub{position:absolute;top:346px;left:0;width:1200px;text-align:center;color:var(--white);font-size:22px;line-height:36px}
.social-rail{position:absolute;left:72px;top:266px;display:flex;flex-direction:column;gap:28px;align-items:center}
.social-rail span{width:12px;height:12px;border-radius:50%;background:var(--white)}
.rail-line{position:absolute;left:78px;top:425px;width:1px;height:60px;background:var(--white)}
.follow{position:absolute;left:40px;top:510px;color:var(--white);font-size:13px;transform:rotate(-90deg);transform-origin:center}
.dot{position:absolute;border-radius:50%;background:var(--white)}

/* about */
.about-photo{position:absolute;left:600px;top:772px;width:497px;height:443px;background:linear-gradient(180deg,#2c3d6e 0%,#4b4a5e 45%,#a57c3d 70%,#26344d 100%)}
.about-frame{position:absolute;left:617px;top:788px;width:463px;height:412px;border:3px solid var(--gold)}
.about-card{position:absolute;left:97px;top:815px;width:575px;height:357px;background:var(--white);box-shadow:0 4px 18px rgba(0,0,0,.2);padding:60px 42px}
.about-card h2{font-size:30px;font-weight:700;color:var(--ink);margin-bottom:14px}
.about-card p{font-size:15px;line-height:30px;color:var(--text)}

/* projects */
.projects{position:absolute;left:0;top:1305px;width:1200px;height:548px;background:linear-gradient(180deg,var(--gold),var(--gold-deep))}
.section-title{position:absolute;left:0;width:1200px;text-align:center;font-size:32px;font-weight:700}
.project{position:absolute;top:1477px;width:310px;height:281px;border:5px solid var(--white);display:flex;align-items:flex-end;justify-content:center;padding-bottom:12px;color:var(--white);font-weight:700;font-size:20px;letter-spacing:.5px}

/* testimonials */
.quote{position:absolute;left:236px;top:1996px;width:728px;text-align:center;font-style:italic;font-size:16px;line-height:31px;color:var(--text)}
.qmark{position:absolute;color:var(--gold);font-size:40px;font-weight:700;font-style:italic}
.avatar{position:absolute;left:520px;top:2122px;width:92px;height:92px;border-radius:50%;background:linear-gradient(160deg,#d9b59a,#8a6a58);box-shadow:0 2px 8px rgba(0,0,0,.25)}
.client{position:absolute;left:640px;top:2160px;font-style:italic;font-size:13px;line-height:16px}

/* blog */
.blog{position:absolute;left:0;top:2302px;width:1200px;height:623px;background:linear-gradient(180deg,#e9e8e6,#f2f0ec 50%,#dfe3e6)}
.post{position:absolute;top:2472px;width:315px}
.post-img{width:315px;height:186px}
.post-date{position:absolute;left:12px;top:173px;width:125px;height:28px;background:var(--gold);color:var(--white);font-size:12px;display:flex;align-items:center;justify-content:center;gap:6px}
.post h3{margin-top:32px;font-size:16px;font-weight:600;color:var(--ink)}
.post p{margin-top:12px;font-size:11.5px;line-height:22px;color:var(--text)}
.post .more{margin-top:10px;font-size:12px;font-weight:700;color:var(--ink)}

/* footer */
.footer{position:absolute;left:0;top:2925px;width:1200px;height:354px;background:var(--footer);color:var(--white)}
.footer h4{position:absolute;top:56px;font-size:20px;font-weight:700}
.footer .small{position:absolute;font-size:12.5px;line-height:25px}
.news-input{position:absolute;left:872px;top:133px;width:228px;height:30px;border:1px solid var(--white);font-size:11px;display:flex;align-items:center;padding-left:8px}
.news-send{position:absolute;right:-1px;top:-1px;width:40px;height:30px;background:var(--gold);display:flex;align-items:center;justify-content:center}
.foot-social{position:absolute;left:874px;top:186px;display:flex;gap:7px}
.foot-social span{width:11px;height:11px;background:var(--white);border-radius:2px}
.foot-line{position:absolute;left:80px;top:255px;width:1030px;height:1px;background:rgba(255,255,255,.3)}
.foot-links{position:absolute;top:272px;left:0;width:1200px;text-align:center;font-size:12.5px;word-spacing:4px}
.copy{position:absolute;top:308px;left:0;width:1200px;text-align:center;font-size:12.5px}
</style>
</head>
<body>

<header class="hero" role="img" aria-label="Modern apartment buildings at dusk">
  <div class="hero-shade"></div>
</header>
<div class="brand"><span class="brand-mark"></span>VORNELIX</div>
<nav class="nav"><span class="active">Home</span><span>About us</span><span>Project</span><span>Contact us</span></nav>
<div class="social-rail"><span></span><span></span><span></span><span></span></div>
<div class="rail-line"></div>
<div class="follow">Follow us</div>
<h1 class="hero-title">VORNELIX CAPITAL</h1>
<p class="hero-sub">Sed ut perspiciatis unde omnis iste natus error sit<br>voluptatem accusantium doloremque</p>
<div class="btn" style="left:510px;top:431px;width:162px;height:52px;font-size:17px">Read More</div>
<div class="dot" style="left:1126px;top:368px;width:10px;height:10px"></div>
<div class="dot" style="left:1118px;top:398px;width:26px;height:26px;background:none;border:2px solid var(--white)"></div>
<div class="dot" style="left:1125px;top:405px;width:12px;height:12px"></div>
<div class="dot" style="left:1126px;top:440px;width:10px;height:10px"></div>

<section>
  <div class="about-photo" role="img" aria-label="Luxury villa with pool lit at dusk"></div>
  <div class="about-frame"></div>
  <div class="about-card">
    <h2>ABOUT US</h2>
    <p>Sed ut perspiciatis unde omnis iste natus error sit voluptatem accusantium doloremque laudantium, totam rem aperiam, eaque ipsa quae ab illo inventore veritatis et quasi architecto beatae vitae dicta sunt explicabo.</p>
  </div>
  <div class="btn" style="left:138px;top:1063px;width:132px;height:44px;font-size:14px">Read More</div>
</section>

<section class="projects" role="img" aria-label="Faint building construction lines on gold"></section>
<h2 class="section-title" style="top:1385px;color:var(--white)">OUR PROJECTS</h2>
<div class="project" style="left:102px;background:linear-gradient(180deg,#7fa9d8 0%,#e7e7e9 45%,#8c8f96 100%)" role="img" aria-label="Apartment building">APPARTMENTS</div>
<div class="project" style="left:445px;background:linear-gradient(180deg,#3c7fd0 0%,#e9e3d6 45%,#2fa7c9 80%,#1c7fa8 100%)" role="img" aria-label="Hotel with pool">HOTELS</div>
<div class="project" style="left:788px;background:linear-gradient(180deg,#6d95c4 0%,#d7b17e 50%,#8d6a47 80%,#4aa0c2 100%)" role="img" aria-label="Commercial building">COMMERCIAL BUILDINGS</div>

<section>
  <h2 class="section-title" style="top:1936px;color:var(--ink);font-size:30px">TESTIMONIALS</h2>
  <span class="qmark" style="left:202px;top:1980px">“</span>
  <p class="quote">Lorem Ipsum is simply dummy text of the printing and typesetting industry. Lorem Ipsum has been the industry's standard dummy text ever since the 1500s, when an unknown printer took a galley of type and scrambled it to make a typespecimen book...</p>
  <span class="qmark" style="left:964px;top:2062px">”</span>
  <svg class="abs" style="left:970px;top:2118px" width="28" height="14" viewBox="0 0 28 14"><circle cx="6" cy="7" r="5.5" fill="#333"/><circle cx="20" cy="7" r="5.5" fill="#333"/><path d="M7.5 4.5 5 7l2.5 2.5M18.5 4.5 21 7l-2.5 2.5" stroke="#fff" stroke-width="1.4" fill="none"/></svg>
  <div class="avatar" role="img" aria-label="Client portrait"></div>
  <div class="client">– MARCUS HALE<br>satisfied customer</div>
</section>

<section class="blog" role="img" aria-label="Faded resort building background"></section>
<h2 class="section-title" style="top:2385px;color:var(--ink);font-size:30px">OUR BLOG</h2>
<article class="post" style="left:98px">
  <div class="post-img" role="img" aria-label="Calculator and financial charts" style="background:linear-gradient(135deg,#f3f4f7,#b9c2d2 60%,#7c8aa6)"></div>
  <div class="post-date">▦ Sep 17 2018</div>
  <h3>SED UT PERSPICIATIS UND</h3>
  <p>Sed ut perspiciatis unde omnis iste natus error sit voluptatem accusantium doloremque laudantium, totam rem aperiam, eaque ipsa quae ab illo</p>
  <div class="more">READ MORE</div>
</article>
<article class="post" style="left:442px">
  <div class="post-img" role="img" aria-label="Resort hotel with pool" style="background:linear-gradient(180deg,#4b8ed6,#e3dccb 50%,#2ea5c8)"></div>
  <div class="post-date">▦ Sep 17 2018</div>
  <h3>SED UT PERSPICIATIS UND</h3>
  <p>Sed ut perspiciatis unde omnis iste natus error sit voluptatem accusantium doloremque laudantium, totam rem aperiam, eaque ipsa quae ab illo</p>
  <div class="more">READ MORE</div>
</article>
<article class="post" style="left:786px">
  <div class="post-img" role="img" aria-label="Villa with pool at sunset" style="background:linear-gradient(180deg,#7098c4,#d9b27c 55%,#5aa3c1)"></div>
  <div class="post-date">▦ Sep 17 2018</div>
  <h3>SED UT PERSPICIATIS UND</h3>
  <p>Sed ut perspiciatis unde omnis iste natus error sit voluptatem accusantium doloremque laudantium, totam rem aperiam, eaque ipsa quae ab illo</p>
  <div class="more">READ MORE</div>
</article>

<footer class="footer">
  <div class="brand" style="left:176px;top:80px;font-size:26px"><span class="brand-mark" style="width:14px;height:14px"></span>VORNELIX</div>
  <p class="small" style="left:100px;top:162px;width:320px">Sed ut perspiciatis unde omnis iste natus error sit voluptatem accusantium doloremque laudantium, totam rem aperiam.</p>
  <h4 style="left:516px">GET IN TOUCH</h4>
  <p class="small" style="left:516px;top:98px;font-weight:500">Phone : (555) 010-2040</p>
  <p class="small" style="left:516px;top:128px;font-weight:500">Email: info@vornelixcapital.com</p>
  <p class="small" style="left:516px;top:157px;line-height:18px;font-weight:500">Address: 1250 Harwell Avenue<br>Oak Ridge, Arkansas<br>AR 70000</p>
  <h4 style="left:872px">NEWSLETTER</h4>
  <p class="small" style="left:872px;top:98px;font-size:11px">SIGN UP YOUR NEWSLETTER</p>
  <div class="news-input">EMAIL ADDRESS
    <div class="news-send"><svg width="14" height="14" viewBox="0 0 14 14"><path d="M1 7 13 1 9 13 7 8z" fill="#fff"/></svg></div>
  </div>
  <div class="foot-social"><span></span><span></span><span></span><span></span></div>
  <div class="foot-line"></div>
  <div class="foot-links">Home &nbsp;&nbsp;|&nbsp;&nbsp; About us &nbsp;&nbsp;|&nbsp;&nbsp; Projects &nbsp;&nbsp;|&nbsp;&nbsp; Contact</div>
  <div class="copy">Copyrights © 2018. All rights reserved.</div>
</footer>

</body>
</html>
```